Unternehmen für Ordnung und Sauberkeit am Arbeitsplatz und Produkte zur Produktionsoptimierung benötigt Visitenkarten und Briefpapier
Zielgruppe
Produkte für Ordnung und Sauberkeit am Arbeitsplatz, Organisation von Arbeitsplätzen, Produkte zur Vereinfachung von Arbeitsabläufen, Produkte zur Produktionsoptimierung unter dem Lean Gedanke, Schlagwort: "5S", nachhaltig, sauber
Aufgabenstellung
Wir sind auf der Suche nach Visitenkarten und Briefpapier für das Unternehmen yourTidor. Nachhaltig, Sauber usw.. Unser Firmenlogo finden Sie anbei.

```html
<!DOCTYPE html>
<html lang="de">
<head>
<meta charset="utf-8">
<title>yourTidor – Briefpapier und Kuvert</title>
<link rel="stylesheet" href="https://fonts.googleapis.com/css2?family=Source+Sans+3:wght@400;700;800&family=Arimo:wght@400&display=swap">
<style>
  :root {
    --brand-green: #1f9a2e;
    --brand-grey: #666666;
    --text-grey: #707070;
    --paper: #ffffff;
    --page-bg: #ffffff;
    --edge: #c9c9c9;
    --mark: #555555;
    --rule: #8a96a8;
  }
  html, body {
    margin: 0;
    padding: 0;
    width: 1200px;
    height: 1000px;
    overflow: hidden;
    background: var(--page-bg);
  }
  .stationery { display: block; width: 1200px; height: 1000px; }
  .crop-mark { stroke: var(--mark); stroke-width: 0.8; }
  .crop-mark.dashed { stroke-dasharray: 4 5; }
  .sheet { fill: var(--paper); }
  .sheet-edge { fill: none; stroke: var(--edge); stroke-width: 0.8; }
  .band-green { fill: var(--brand-green); }
  .band-grey { fill: var(--brand-grey); }
  .wordmark {
    font-family: "Source Sans 3", sans-serif;
    font-weight: 800;
    fill: var(--brand-green);
  }
  .wordmark.muted { fill: #7a7a7a; }
  .body-text {
    font-family: "Source Sans 3", sans-serif;
    font-weight: 400;
    fill: var(--text-grey);
  }
  .address-text {
    font-family: "Arimo", sans-serif;
    font-weight: 400;
    fill: #5a5a5a;
  }
  .divider { stroke: var(--rule); stroke-width: 0.9; }
  .icon-tile { fill: var(--brand-grey); }
  .icon-glyph { fill: #ffffff; }
  .window { fill: #ffffff; stroke: #b5b5b5; stroke-width: 1; }
</style>
</head>
<body>
<svg class="stationery" viewBox="0 0 1200 1000" xmlns="http://www.w3.org/2000/svg">
  <defs>
    <filter id="paper-shadow" x="-5%" y="-5%" width="112%" height="112%">
      <feDropShadow dx="3" dy="3" stdDeviation="2.5" flood-color="#000" flood-opacity="0.28"/>
    </filter>
    <filter id="window-inset" x="-5%" y="-5%" width="110%" height="110%">
      <feDropShadow dx="-2" dy="-2" stdDeviation="2" flood-color="#000" flood-opacity="0.25"/>
    </filter>
  </defs>

  <!-- Letterhead -->
  <g class="letterhead">
    <g class="crop-marks">
      <line class="crop-mark" x1="96" y1="165" x2="96" y2="190"/>
      <line class="crop-mark" x1="516" y1="165" x2="516" y2="190"/>
      <line class="crop-mark" x1="96" y1="810" x2="96" y2="835"/>
      <line class="crop-mark" x1="516" y1="810" x2="516" y2="835"/>
      <line class="crop-mark" x1="58" y1="203" x2="83" y2="203"/>
      <line class="crop-mark" x1="529" y1="203" x2="555" y2="203"/>
      <line class="crop-mark" x1="58" y1="797" x2="83" y2="797"/>
      <line class="crop-mark" x1="529" y1="797" x2="555" y2="797"/>
      <line class="crop-mark" x1="88" y1="406" x2="110" y2="406"/>
      <line class="crop-mark" x1="88" y1="595" x2="110" y2="595"/>
    </g>

    <rect class="sheet" x="96" y="203" width="420" height="594" filter="url(#paper-shadow)"/>
    <polygon class="band-green" points="96,203 107,203 107,351 96,343"/>
    <polygon class="band-grey" points="96,347 107,356 107,797 96,797"/>

    <g class="brand-mark">
      <rect x="134" y="241" width="22" height="22" rx="4" fill="var(--brand-green)"/>
      <text class="wordmark" x="162" y="262" font-size="27" textLength="120" lengthAdjust="spacingAndGlyphs">yourTidor</text>
    </g>

    <g class="contact-block">
      <line class="divider" x1="397" y1="231" x2="397" y2="327"/>
      <rect class="icon-tile" x="403" y="231" width="11" height="11" rx="2.5"/>
      <path class="icon-glyph" d="M408.5 233.3a2.6 2.6 0 0 1 2.6 2.6c0 1.9-2.6 4.3-2.6 4.3s-2.6-2.4-2.6-4.3a2.6 2.6 0 0 1 2.6-2.6z"/>
      <circle cx="408.5" cy="235.9" r="0.9" fill="var(--brand-grey)"/>
      <text class="wordmark" x="418" y="240.5" font-size="10.5" textLength="37" lengthAdjust="spacingAndGlyphs">yourTidor</text>
      <text class="body-text" x="417" y="249.5" font-size="6.6">Lindenhofweg 12</text>
      <text class="body-text" x="417" y="258.5" font-size="6.6">95030 Hofheim</text>

      <rect class="icon-tile" x="403" y="263.5" width="11" height="11" rx="2.5"/>
      <path class="icon-glyph" d="M405 267.5h7v1.6h-1.4v-0.7h-4.2v0.7H405z M406 269.8h5l0.6 3h-6.2z"/>
      <text class="body-text" x="416" y="271.8" font-size="6.6">04120 / 55810 2</text>

      <rect class="icon-tile" x="403" y="276" width="11" height="11" rx="2.5"/>
      <rect x="405.5" y="278.5" width="6" height="6" fill="none" stroke="#fff" stroke-width="0.8"/>
      <line x1="406.5" y1="280.3" x2="410.5" y2="280.3" stroke="#fff" stroke-width="0.6"/>
      <line x1="406.5" y1="282.3" x2="410.5" y2="282.3" stroke="#fff" stroke-width="0.6"/>
      <text class="body-text" x="416" y="284.4" font-size="6.6">04120 / 55810 / 3 7</text>

      <rect class="icon-tile" x="403" y="288.5" width="11" height="11" rx="2.5"/>
      <text x="408.5" y="297.2" font-size="9" text-anchor="middle" font-family="Arimo, sans-serif" fill="#fff">@</text>
      <text class="body-text" x="416" y="296.8" font-size="6.6">info@ordnung-plus.de</text>

      <rect class="icon-tile" x="403" y="301.5" width="11" height="11" rx="2.5"/>
      <circle cx="408.5" cy="307" r="3.2" fill="none" stroke="#fff" stroke-width="0.7"/>
      <line x1="405.3" y1="307" x2="411.7" y2="307" stroke="#fff" stroke-width="0.6"/>
      <ellipse cx="408.5" cy="307" rx="1.4" ry="3.2" fill="none" stroke="#fff" stroke-width="0.6"/>
      <text class="body-text" x="417.5" y="309.6" font-size="6.6">www.ordnungplus-shop.at</text>
    </g>

    <g class="letter-footer">
      <rect x="186" y="766" width="8" height="8" rx="1.5" fill="var(--brand-green)"/>
      <text class="wordmark" x="197" y="773.5" font-size="10" textLength="38" lengthAdjust="spacingAndGlyphs">yourTidor</text>
      <line class="divider" x1="243" y1="760" x2="243" y2="782"/>
      <text class="body-text" x="256" y="765.5" font-size="5.8">Kreisbank Oberland</text>
      <text class="body-text" x="256" y="773.8" font-size="5.8">BLZ 000 700 00</text>
      <text class="body-text" x="256" y="782.1" font-size="5.8">Kto 300000000</text>
      <line class="divider" x1="339" y1="760" x2="339" y2="782"/>
      <text class="body-text" x="352" y="769.5" font-size="5.8">IBAN: AT483120700050081234</text>
      <text class="body-text" x="352" y="777.8" font-size="5.8">BIC: KROBAT2GXXX</text>
    </g>
  </g>

  <!-- Envelope front -->
  <g class="envelope-front">
    <g class="crop-marks">
      <line class="crop-mark" x1="654" y1="216" x2="654" y2="241"/>
      <line class="crop-mark" x1="1103" y1="216" x2="1103" y2="241"/>
      <line class="crop-mark dashed" x1="615" y1="254" x2="641" y2="254"/>
      <line class="crop-mark dashed" x1="1116" y1="254" x2="1142" y2="254"/>
      <line class="crop-mark" x1="615" y1="485" x2="641" y2="485"/>
      <line class="crop-mark" x1="1116" y1="485" x2="1142" y2="485"/>
      <line class="crop-mark" x1="654" y1="497" x2="654" y2="523"/>
      <line class="crop-mark" x1="1103" y1="497" x2="1103" y2="523"/>
    </g>

    <path class="sheet" filter="url(#paper-shadow)" d="M654 254 L672 192 Q675 183 684 183 L1073 183 Q1082 183 1085 192 L1103 254 L1103 485 L654 485 Z"/>
    <path class="sheet-edge" d="M654 254 L672 192 Q675 183 684 183 L1073 183 Q1082 183 1085 192 L1103 254 Z"/>

    <g class="flap-mark" transform="rotate(180 878 221)">
      <text class="wordmark muted" x="878" y="228" font-size="20" text-anchor="middle" textLength="80" lengthAdjust="spacingAndGlyphs">yourTidor</text>
    </g>

    <g class="sender-line">
      <path fill="var(--brand-grey)" d="M686 279.5a4.6 4.6 0 0 1 4.6 4.6c0 3.2-4.6 6.6-4.6 6.6s-4.6-3.4-4.6-6.6a4.6 4.6 0 0 1 4.6-4.6z"/>
      <circle cx="686" cy="284" r="1.7" fill="#fff"/>
      <text class="wordmark" x="695" y="288.5" font-size="10.5" textLength="37" lengthAdjust="spacingAndGlyphs">yourTidor</text>
      <text class="body-text" x="695" y="296.5" font-size="6">Lindenhofweg 12</text>
      <text class="body-text" x="695" y="305.5" font-size="6">95030 Hofheim</text>
    </g>

    <rect class="window" x="681" y="384" width="180" height="72" rx="9" filter="url(#window-inset)"/>
    <g class="recipient">
      <text class="address-text" x="716.5" y="406.5" font-size="6.2">Marlene Brückner</text>
      <text class="address-text" x="716.5" y="416.2" font-size="6.2">Am Mühlenbach 27</text>
      <text class="address-text" x="716.5" y="425.9" font-size="6.2">53819 Neunkirchen</text>
      <text class="address-text" x="716.5" y="435.6" font-size="6.2">SCHWEIZ</text>
    </g>

    <g class="brand-mark">
      <rect x="943" y="404" width="19" height="19" rx="3.5" fill="var(--brand-green)"/>
      <text class="wordmark" x="967" y="422" font-size="23" textLength="103" lengthAdjust="spacingAndGlyphs">yourTidor</text>
    </g>

    <polygon class="band-green" points="654,477 952,477 946,485 654,485"/>
    <polygon class="band-grey" points="956,477 1103,477 1103,485 950,485"/>
  </g>

  <!-- Envelope back -->
  <g class="envelope-back">
    <g class="crop-marks">
      <line class="crop-mark" x1="654" y1="528" x2="654" y2="553"/>
      <line class="crop-mark" x1="1103" y1="528" x2="1103" y2="553"/>
      <line class="crop-mark dashed" x1="615" y1="566" x2="641" y2="566"/>
      <line class="crop-mark dashed" x1="1116" y1="566" x2="1142" y2="566"/>
      <line class="crop-mark" x1="615" y1="797" x2="641" y2="797"/>
      <line class="crop-mark" x1="1116" y1="797" x2="1142" y2="797"/>
      <line class="crop-mark" x1="654" y1="810" x2="654" y2="835"/>
      <line class="crop-mark" x1="1103" y1="810" x2="1103" y2="835"/>
    </g>

    <rect class="sheet" x="654" y="566" width="449" height="231" filter="url(#paper-shadow)"/>
    <path class="sheet" filter="url(#paper-shadow)" d="M654 566 L1103 566 L1085 628 Q1082 637 1073 637 L684 637 Q675 637 672 628 Z"/>

    <text class="wordmark muted" x="878" y="605" font-size="20" text-anchor="middle" textLength="80" lengthAdjust="spacingAndGlyphs">yourTidor</text>
  </g>
</svg>
</body>
</html>
```